Stationery Design Project for Nimbora, Chicago

Nimbora, a street parking application which helps car drivers find a street parking spot by offering an ideal path along which to look for parking. This path is calculated by our algorithm based on data (e.g. historical data, baseball games schedule, etc.). Along this path the driver will find a spot and will also save 70% of the search time. Customer we target is reg. between 21 and 45 yo.

We envision something young, fresh, bright and original. Slightly abstract maybe. It should represent the idea and elements of finding street parking in the city, e.g. car(s), parking spot, people, city, etc. (just ideas!).

Logo is attached.

Requirement:
- Business Cards (2 Sided Full Color CMYK)
- Letterhead (1 Sided Full Color CMYK)
- Envelope (1 Sided Full Color CMYK)
- Sticker (1 Sided Full Color CMYK), round with a 2inch diameter.

Reason: We're starting to get more and more designs and need more time to look into all of them. Very exciting!! Thanks to everybody!

Hi all, we're in the process of selecting our favs. Though choices!!! Really good submissions. Will keep you posted and sorry for the delay.

Target Market(s)

Car drivers and owners between 21 and 45

Industry/Entity Type

Parking

Requirements
Must have
• Sticker should be round and include company URL nimbora.com and the new logo which we will attach soon.
Should not have
• Should not be too serious or boring.

```html
<!DOCTYPE html>
<html lang="en">
<head>
<meta charset="utf-8">
<title>Nimbora Business Card</title>
<link rel="stylesheet" href="https://fonts.googleapis.com/css2?family=Source+Sans+3:wght@400;600;700&display=swap">
<style>
  :root {
    --page-bg: #e9e6e2;
    --card-white: #ffffff;
    --ink: #3b3b3b;
    --ink-soft: #4a4a4a;
    --blue-deep: #24399a;
    --blue-mid: #2f55c4;
    --blue-sky: #2b9bd6;
    --blue-bright: #1c6fd8;
    --swoosh-grey: #3a3a3a;
    --divider: #b5b5b5;
    --photo-dark: #55585c;
    --photo-light: #8d9196;
  }
  * { margin: 0; padding: 0; box-sizing: border-box; }
  html, body {
    width: 1200px; height: 1063px; overflow: hidden;
    background: var(--page-bg);
    font-family: "Source Sans 3", "Myriad Pro", sans-serif;
  }
  .canvas { position: relative; width: 1200px; height: 1063px; }

  .card {
    position: absolute;
    width: 763px; height: 436px;
    border-radius: 28px;
    overflow: hidden;
    box-shadow: 0 6px 18px rgba(0,0,0,0.22);
  }

  /* Front */
  .card--front { left: 70px; top: 77px; background: var(--card-white); }
  .card__waves { position: absolute; inset: 0; }
  .brand {
    position: absolute; left: 134px; top: 40px;
    display: flex; align-items: center; gap: 22px;
  }
  .brand__dot {
    width: 136px; height: 136px; border-radius: 50%;
    background: var(--blue-bright);
  }
  .brand__name {
    font-size: 84px; font-weight: 600; color: var(--ink);
    letter-spacing: 1px; line-height: 1;
  }
  .address {
    position: absolute; right: 401px; top: 245px;
    text-align: right; font-size: 18px; line-height: 25px; color: var(--ink-soft);
  }
  .contact-divider {
    position: absolute; left: 387px; top: 218px;
    width: 1px; height: 112px; background: var(--divider);
  }
  .contact {
    position: absolute; left: 408px; top: 220px;
    list-style: none; font-size: 19px; color: var(--ink-soft);
  }
  .contact li { display: flex; align-items: center; gap: 10px; height: 27.5px; }
  .contact svg { width: 15px; height: 15px; fill: var(--ink-soft); flex: none; }
  .holder {
    position: absolute; left: 265px; top: 390px;
    color: #fff; font-size: 24px; font-weight: 700;
  }
  .holder__title { font-size: 19px; font-weight: 400; }

  /* Back */
  .card--back {
    left: 348px; top: 562px;
    background: linear-gradient(90deg, var(--blue-sky) 0%, #2a86cf 45%, var(--blue-deep) 100%);
  }
  .back-mark {
    position: absolute; left: 52px; top: 105px;
    width: 218px; height: 218px; border-radius: 50%;
    background: var(--blue-bright);
    box-shadow: 0 0 0 10px rgba(255,255,255,0.18);
    display: flex; align-items: center; justify-content: center;
  }
  .back-mark__name { color: #fff; font-size: 38px; font-weight: 600; }
  .lot-photo {
    position: absolute; left: 336px; top: 67px;
    width: 430px; height: 303px;
    background: radial-gradient(ellipse at 50% 50%, var(--photo-light) 0%, var(--photo-dark) 70%, rgba(85,88,92,0) 100%);
    -webkit-mask-image: linear-gradient(90deg, transparent 0, #000 40px);
            mask-image: linear-gradient(90deg, transparent 0, #000 40px);
  }
</style>
</head>
<body>
<div class="canvas">

  <section class="card card--front">
    <svg class="card__waves" viewBox="0 0 763 436" preserveAspectRatio="none" aria-hidden="true">
      <defs>
        <linearGradient id="bandBlue" x1="0" x2="1" y1="0" y2="0">
          <stop offset="0" stop-color="#2a3f9f"/>
          <stop offset="0.5" stop-color="#3060cc"/>
          <stop offset="1" stop-color="#24399a"/>
        </linearGradient>
      </defs>
      <path d="M0 288 C 200 318, 430 350, 763 370 L763 436 L0 436 Z" fill="var(--swoosh-grey)"/>
      <path d="M0 300 C 220 345, 460 372, 763 372 L763 436 L0 436 Z" fill="#ffffff"/>
      <path d="M0 312 C 230 368, 480 384, 763 366 L763 436 L0 436 Z" fill="url(#bandBlue)"/>
    </svg>

    <div class="brand">
      <div class="brand__dot"></div>
      <span class="brand__name">nimbora</span>
    </div>

    <p class="address">Complex Name, Street Name<br>Area, City Name,000 000</p>
    <div class="contact-divider"></div>
    <ul class="contact">
      <li><svg viewBox="0 0 16 16"><path d="M3 1l3 3-1.5 2a9 9 0 005.5 5.5L12 10l3 3-2 2C7 15 1 9 1 3z"/></svg>+91 12345 67890</li>
      <li><svg viewBox="0 0 16 16"><path d="M4 1h8v14H4zM5.5 3v8h5V3z"/></svg>+91 12345 67890</li>
      <li><svg viewBox="0 0 16 16"><path d="M1 3h14v10H1zM2.5 4.5L8 9l5.5-4.5z"/></svg>info@nimbora.com</li>
      <li><svg viewBox="0 0 16 16"><circle cx="8" cy="8" r="7"/></svg>www.nimbora.com</li>
    </ul>
    <p class="holder">Your Name , <span class="holder__title">Title</span></p>
  </section>

  <section class="card card--back">
    <div class="back-mark"><span class="back-mark__name">nimbora</span></div>
    <div class="lot-photo" role="img" aria-label="Aerial photo of cars parked in rows in a parking lot"></div>
  </section>

</div>
</body>
</html>
```